Calm Harbor Bodywork business is seeking a Business Card Design

We are a new natural therapy business that needs a Business Card Design with an appointment card on the back.

We offer Myotherapy (muscle therapy) services and have a strong focus and commitment to helping people relieve pain and restore movement to their bodies.

I am attaching my business logo for you information.

Business card must contain my logo and have space for name, title, qualifications, phone number, email, web address

Appointment Card on the back of the card must contain space to write next appointment date, time and name of therapist and cancellation policy.

Cancellation Policy
Minimum of 24hrs notice is required prior to appointment time or full treatment fees with apply.

```html
<!DOCTYPE html>
<html lang="en">
<head>
<meta charset="utf-8">
<title>Calm Harbor Bodywork – Business &amp; Appointment Card</title>
<link rel="stylesheet" href="https://fonts.googleapis.com/css2?family=Lato:wght@400;700;900&display=swap">
<style>
  :root {
    --bg: #2a2a2a;
    --paper: #f7f7f5;
    --green: #78b233;
    --green-dark: #5e9a22;
    --red: #c0202f;
    --brown: #4e3f38;
    --ink: #2b2b2b;
    --white: #ffffff;
  }
  * { box-sizing: border-box; margin: 0; padding: 0; }
  html, body { width: 1200px; height: 900px; overflow: hidden; }
  body {
    background: var(--bg);
    font-family: "Lato", Arial, sans-serif;
    position: relative;
  }
  .card {
    position: absolute;
    width: 600px;
    height: 340px;
    background: var(--paper);
    overflow: hidden;
    box-shadow: 0 10px 30px rgba(0,0,0,.5);
  }
  .card--back { left: 300px; top: 70px; }
  .card--front { left: 300px; top: 480px; }

  /* ---------- back: appointment card ---------- */
  .label {
    position: absolute;
    background: var(--green);
    color: var(--white);
    font-weight: 900;
    text-transform: uppercase;
    letter-spacing: .5px;
    padding: 3px 8px;
    font-size: 17px;
  }
  .label--appointment { left: 34px; top: 30px; }
  .label--policy { left: 34px; top: 196px; font-size: 15px; }
  .field {
    position: absolute;
    font-size: 14px;
    color: var(--ink);
    text-transform: uppercase;
    display: flex;
    align-items: flex-end;
    gap: 4px;
  }
  .field .dots {
    display: inline-block;
    border-bottom: 2px dotted var(--ink);
    height: 1px;
    margin-bottom: 4px;
  }
  .field--date { left: 34px; top: 76px; }
  .field--date .dots { width: 200px; }
  .field--time { left: 300px; top: 76px; }
  .field--time .dots { width: 230px; }
  .field--therapist { left: 34px; top: 160px; }
  .field--therapist .dots { width: 360px; }
  .checks {
    position: absolute;
    left: 34px;
    top: 113px;
    display: flex;
    gap: 9px;
    font-weight: 700;
    font-size: 13px;
    color: var(--ink);
  }
  .check { display: flex; align-items: center; gap: 5px; }
  .check::after {
    content: "";
    width: 18px; height: 18px;
    border: 2px solid var(--green);
    border-radius: 3px;
    background: var(--white);
  }
  .policy-text {
    position: absolute;
    left: 34px; top: 230px;
    width: 245px;
    font-size: 14px;
    line-height: 1.35;
    font-weight: 700;
    color: var(--ink);
  }

  /* ---------- brand lockup ---------- */
  .brand { position: absolute; display: flex; align-items: center; gap: 10px; }
  .brand__mark { background: var(--red); flex-shrink: 0; }
  .brand__name { color: var(--red); font-weight: 900; line-height: 1.05; }
  .brand--back { right: 30px; bottom: 40px; }
  .brand--back .brand__mark { width: 46px; height: 46px; }
  .brand--back .brand__name { font-size: 20px; }
  .brand--front { left: 30px; top: 130px; }
  .brand--front .brand__mark { width: 64px; height: 64px; }
  .brand--front .brand__name { font-size: 26px; width: 180px; }

  /* ---------- front: contact side ---------- */
  .front-panel { position: absolute; inset: 0; }
  .person { position: absolute; left: 370px; top: 30px; text-align: center; width: 200px; }
  .person__name { color: var(--red); font-weight: 900; font-size: 21px; }
  .person__title { color: var(--white); font-weight: 700; font-size: 13px; letter-spacing: .5px; }
  .contact {
    position: absolute;
    display: flex; align-items: center; gap: 12px;
    color: var(--white); font-weight: 700; font-size: 13px; line-height: 1.3;
    white-space: nowrap;
  }
  .contact__icon {
    width: 34px; height: 34px;
    border: 2px solid var(--white);
    border-radius: 4px;
    display: flex; align-items: center; justify-content: center;
    flex-shrink: 0;
  }
  .contact__icon--red { background: var(--red); }
  .contact__icon--brown { background: var(--brown); }
  .contact__icon--green { background: var(--green-dark); }
  .contact--phone { left: 312px; top: 100px; }
  .contact--mail { left: 314px; top: 150px; }
  .contact--web { left: 314px; top: 200px; }
  .contact--address { left: 318px; top: 254px; }
</style>
</head>
<body>

<section class="card card--back" aria-label="Appointment card">
  <div class="label label--appointment">Next Appointment</div>
  <div class="field field--date">Date: <span class="dots"></span></div>
  <div class="field field--time">Time: <span class="dots"></span></div>
  <div class="checks">
    <span class="check">Mon</span><span class="check">Tue</span><span class="check">Wed</span>
    <span class="check">Thu</span><span class="check">Fri</span><span class="check">Sat</span>
    <span class="check">Sun</span><span class="check">AM</span><span class="check">PM</span>
  </div>
  <div class="field field--therapist">Name of Therapist: <span class="dots"></span></div>
  <div class="label label--policy">Cancellation Policy</div>
  <p class="policy-text">Minimum of 24hrs notice is required prior to appointment time or full treatment fees will apply</p>
  <div class="brand brand--back">
    <span class="brand__mark"></span>
    <span class="brand__name">Calm Harbor<br>Bodywork</span>
  </div>
</section>

<section class="card card--front" aria-label="Business card">
  <svg class="front-panel" width="600" height="340" viewBox="0 0 600 340" aria-hidden="true">
    <path d="M300 0 H600 V340 H345 C320 290 318 230 328 175 C338 120 330 60 300 0 Z" fill="var(--green)"/>
    <path d="M300 0 C330 60 338 120 328 175 C318 230 320 290 345 340" fill="none" stroke="var(--red)" stroke-width="8"/>
  </svg>

  <div class="brand brand--front">
    <span class="brand__mark"></span>
    <span class="brand__name">Calm Harbor Bodywork</span>
  </div>

  <div class="person">
    <div class="person__name">YOUR NAME</div>
    <div class="person__title">DESIGNATION</div>
  </div>

  <div class="contact contact--phone">
    <span class="contact__icon contact__icon--red">
      <svg width="20" height="20" viewBox="0 0 24 24"><path fill="#fff" d="M6.6 10.8a15 15 0 0 0 6.6 6.6l2.2-2.2c.3-.3.7-.4 1-.2 1.1.4 2.3.6 3.6.6.6 0 1 .4 1 1V20c0 .6-.4 1-1 1A17 17 0 0 1 3 4c0-.6.4-1 1-1h3.5c.6 0 1 .4 1 1 0 1.3.2 2.5.6 3.6.1.3 0 .7-.2 1z"/></svg>
    </span>
    <span>+61 400 555 019</span>
  </div>
  <div class="contact contact--mail">
    <span class="contact__icon contact__icon--brown">
      <svg width="20" height="16" viewBox="0 0 24 18"><rect x="1" y="1" width="22" height="16" fill="none" stroke="#fff" stroke-width="2"/><path d="M1 1l11 9 11-9" fill="none" stroke="#fff" stroke-width="2"/></svg>
    </span>
    <span>info@calmharborbodywork.com.au</span>
  </div>
  <div class="contact contact--web">
    <span class="contact__icon contact__icon--green">
      <svg width="20" height="20" viewBox="0 0 24 24"><circle cx="12" cy="12" r="10" fill="none" stroke="#fff" stroke-width="2"/><ellipse cx="12" cy="12" rx="4" ry="10" fill="none" stroke="#fff" stroke-width="1.5"/><path d="M2 12h20" stroke="#fff" stroke-width="1.5"/></svg>
    </span>
    <span>www.calmharborbodywork.com.au</span>
  </div>
  <div class="contact contact--address">
    <span class="contact__icon contact__icon--red">
      <svg width="20" height="20" viewBox="0 0 24 24"><path fill="#fff" d="M12 3l10 9h-3v9h-5v-6h-4v6H5v-9H2z"/></svg>
    </span>
    <span>Level 2/118 Quay St,<br>Seabrook VIC 3999</span>
  </div>
</section>

</body>
</html>
```